Glen Whitmore Professional Coaching

I would like a website with a mountain theme geared towards professional executives reaching higher peaks and goals. This is a 3 page website with brand essence information on the opening page, the coaching process on a second page and "about me" and lead capture form on a third page

Target Market(s)

C-Level audience, involved in tech, government, manufacturing, and transportation type of corporations

Coding

Coded - Design and coding required

Number of Pages Required

3 page

Font styles to use
Sans Serif

Colors
a7a7a7
1b1b1b
e8e8e8
3176b5
abd036
0355a3

Requirements
Must have
• Looking for a user friendly site that I can manage/update going forward. Must have:
• 1. "Is coaching right for you?" - page 1
• 2. "Our Process" page 2 - I will describe how we approach coaching
• 3. "Contact us" page 3 where I can capture contact information from potential clients
• 4. Clean and professional with more modern font
• 5. Links to personal social media sites
• 6. Ability to upload/download .pdf documents as resources
• 7. Ability to add on new pages in the future (such as a blog page)
Nice to have
• I want a place to store articles I write or use.
• LinkedIn or Twitter Feed
Should not have
• Not fluffy or too 'zen' like personal life coaches tend to present.

```html
<!DOCTYPE html>
<html lang="en">
<head>
<meta charset="utf-8">
<title>Glen Whitmore Professional Coaching</title>
<link href="https://fonts.googleapis.com/css2?family=Poppins:wght@400;500;600&family=Roboto:wght@400;700&family=Roboto+Condensed:wght@400&display=swap" rel="stylesheet">
<style>
:root{
  --white:#ffffff;
  --ink:#1b1b1b;
  --grey:#a7a7a7;
  --light:#e8e8e8;
  --sky:#1b9fd6;
  --sky-deep:#0f86c0;
  --teal:#1c958f;
  --teal-deep:#137a76;
  --accent:#1a8fd0;
  --footer:#14191d;
  --rock-dark:#1c2328;
  --rock-mid:#3c4a52;
}
*{box-sizing:border-box;margin:0;padding:0}
html,body{width:1200px;height:3711px;overflow:hidden}
body{font-family:"Poppins",sans-serif;color:var(--white);background:var(--footer)}
.page{position:relative;width:1200px;height:3711px;overflow:hidden}
.layer{position:absolute;left:0;width:1200px}

/* backgrounds */
.hero-scene{top:0;height:760px;background:linear-gradient(160deg,#4d6472 0%,#2e3f49 35%,#5b6f7a 60%,#1f2a30 100%)}
.about-band{top:620px;height:640px;background:linear-gradient(120deg,var(--sky) 0%,#2eaee0 55%,var(--sky-deep) 100%);clip-path:polygon(0 11px,1200px 110px,1200px 543px,0 630px)}
.coaching-scene{top:1150px;height:820px;background:linear-gradient(180deg,#43505a 0%,#2a3a3f 40%,#1f4a4e 70%,#2d3436 100%)}
.testimonial-band{top:1900px;height:660px;background:linear-gradient(180deg,var(--teal) 0%,#23a09a 50%,var(--teal-deep) 100%);clip-path:polygon(0 30px,1200px 5px,1200px 574px,0 648px)}
.blog-scene{top:2470px;height:800px;background:linear-gradient(180deg,#d8e6ee 0%,#f2f6f8 35%,#c9d6de 75%,#8fa2ad 100%)}
.footer-band{top:3150px;height:561px;background:var(--footer);clip-path:polygon(0 17px,1200px 105px,1200px 561px,0 561px)}

/* header */
.logo{position:absolute;left:141px;top:40px;font-family:"Poppins",sans-serif;font-weight:600;font-size:38px;color:var(--white)}
.nav{position:absolute;top:60px;left:618px;display:flex;gap:0;font-family:"Roboto",sans-serif;font-size:17px}
.nav a{color:var(--white);text-decoration:none;position:absolute;white-space:nowrap}
.search{position:absolute;left:1036px;top:58px}

.hero-title{position:absolute;left:141px;top:210px;font-family:"Roboto Condensed",sans-serif;font-size:66px;line-height:74px;color:var(--white)}
.btn-solid{position:absolute;left:141px;top:382px;width:153px;height:38px;border-radius:19px;background:var(--sky);color:var(--white);font-family:"Poppins",sans-serif;font-weight:600;font-size:14px;text-align:center;line-height:38px}
.slider-dots{position:absolute;left:141px;top:461px;display:flex;gap:5px}
.slider-dots span{width:14px;height:14px;border-radius:50%;border:2px solid var(--white)}
.slider-dots span.active{background:var(--white)}

/* about */
.portrait{position:absolute;left:147px;top:765px;width:360px;height:360px;border-radius:50%;border:8px solid var(--white);background:linear-gradient(160deg,#5f8a4a 0%,#3f5f35 45%,#203a5c 100%)}
.about-arrow{position:absolute;left:440px;top:738px}
.about-title{position:absolute;left:569px;top:770px;font-family:"Poppins",sans-serif;font-weight:600;font-size:48px}
.about-text{position:absolute;left:569px;top:848px;width:480px;font-size:15px;line-height:30.5px}
.btn-outline{position:absolute;left:569px;top:1064px;width:154px;height:42px;border:2px solid var(--white);border-radius:21px;font-weight:600;font-size:14px;text-align:center;line-height:38px}

/* section headings */
.section-title{position:absolute;height:64px;border:3px solid var(--white);font-family:"Roboto",sans-serif;font-weight:700;font-size:31px;text-align:center;line-height:58px;color:var(--white)}
.section-title.blue{border-color:var(--accent);color:var(--accent)}

/* coaching cards */
.step-card{position:absolute;width:441px;height:168px;background:var(--white);border-radius:84px;color:var(--ink)}
.step-icon{position:absolute;left:22px;top:24px}
.step-card h3{position:absolute;left:164px;top:20px;font-family:"Poppins",sans-serif;font-weight:600;font-size:19px}
.step-card p{position:absolute;left:164px;top:56px;width:262px;font-size:12.5px;line-height:22px;color:#333}
.step-hub{position:absolute;left:567px;top:1614px}

/* testimonials */
.quote{position:absolute;top:2190px;width:300px}
.avatar{position:absolute;left:0;top:4px;width:70px;height:70px;border-radius:50%;border:3px solid var(--white);background:linear-gradient(160deg,#c69a7c,#5a4034)}
.quote-text{position:absolute;left:86px;top:0;width:220px;font-size:12.5px;line-height:22px}
.quote-text b{font-family:"Roboto",sans-serif;font-size:18px;margin-right:6px}
.quote-name{position:absolute;left:86px;top:106px;font-size:13px;font-style:italic}
.stars{position:absolute;left:86px;top:138px;display:flex;gap:3px}
.carousel-arrows{position:absolute;left:565px;top:2396px;display:flex;gap:10px}

/* blog */
.post{position:absolute;top:2742px;width:426px;height:292px;border:5px solid var(--white);box-shadow:0 4px 14px rgba(0,0,0,.25)}
.post-image{position:absolute;inset:0}
.post-caption{position:absolute;left:40px;top:186px;width:340px;height:128px;background:var(--white);text-align:center;color:var(--ink);box-shadow:0 3px 10px rgba(0,0,0,.15)}
.post-caption h4{font-weight:400;font-size:18px;line-height:30px;margin-top:18px}
.post-meta{margin-top:10px;font-size:13px;color:var(--accent);display:flex;justify-content:center;gap:22px}

/* footer */
.foot-title{position:absolute;top:3288px;font-family:"Roboto",sans-serif;font-weight:700;font-size:23px}
.foot-text{position:absolute;left:143px;top:3348px;width:330px;font-size:12.5px;line-height:22px;color:#d5d5d5}
.signup{position:absolute;left:143px;top:3414px;width:365px;height:40px;border-radius:20px;background:var(--white)}
.signup span{position:absolute;left:18px;top:11px;font-size:12px;color:var(--grey)}
.signup b{position:absolute;right:0;top:0;width:118px;height:40px;border-radius:20px;background:var(--sky);color:var(--white);font-size:13px;text-align:center;line-height:40px;font-weight:600}
.contact-row{position:absolute;left:584px;display:flex;gap:16px;font-size:13px;line-height:22px;color:#e5e5e5}
.contact-row svg{flex:none;margin-top:3px}
.social{position:absolute;left:905px;top:3344px;display:flex;gap:6px}
.social span{width:25px;height:25px;border-radius:50%;border:2px solid #cfcfcf}
.copyright{position:absolute;left:0;top:3624px;width:1200px;text-align:center;font-size:13px;color:#e5e5e5}
</style>
</head>
<body>
<div class="page">
  <div class="layer hero-scene" role="img" aria-label="Climber scaling a rocky cliff face above clouds"></div>
  <div class="layer coaching-scene" role="img" aria-label="Mountain lake valley with pine forest"></div>
  <div class="layer blog-scene" role="img" aria-label="Snowy mountain range under a pale sky"></div>
  <div class="layer about-band"></div>
  <div class="layer testimonial-band"></div>
  <div class="layer footer-band"></div>

  <!-- header -->
  <div class="logo">Glen Whitmore</div>
  <nav class="nav">
    <a style="left:0">HOME</a>
    <a style="left:82px">COACHING PROCESS</a>
    <a style="left:297px">ABOUT ME</a>
  </nav>
  <svg class="search" width="20" height="20" viewBox="0 0 20 20" aria-label="Search"><circle cx="8" cy="8" r="6" fill="none" stroke="#fff" stroke-width="2.5"/><line x1="12.5" y1="12.5" x2="18" y2="18" stroke="#fff" stroke-width="2.5"/></svg>

  <h1 class="hero-title">Glen Whitmore<br>Professional Coaching</h1>
  <div class="btn-solid">READ MORE</div>
  <div class="slider-dots"><span class="active"></span><span></span><span></span><span></span></div>

  <!-- about -->
  <div class="portrait" role="img" aria-label="Portrait of the coach in a navy blazer outdoors"></div>
  <svg class="about-arrow" width="100" height="50" viewBox="0 0 100 50"><path d="M6 46 C14 14 50 4 86 18" fill="none" stroke="#fff" stroke-width="4"/><path d="M72 6 L88 18 L70 28" fill="none" stroke="#fff" stroke-width="4"/></svg>
  <h2 class="about-title">About me</h2>
  <p class="about-text">Nam libero tempore, cum soluta nobis est eligendi optio cumque nihil impedit minus id quod maxime placeat facere possimus, omnis voluptas assumenda est, omnis dolor repellendus. Temporibus autem quibusdam et aut officiis debitis aut rerum necessitatibus saepe eveniet ut et voluptates repudiandae sint et molestiae non recusandae earum rerum hic tenetur.</p>
  <div class="btn-outline">READ MORE</div>

  <!-- coaching process -->
  <div class="section-title" style="left:413px;top:1324px;width:370px">COACHING PROCESS</div>

  <div class="step-card" style="left:143px;top:1460px">
    <svg class="step-icon" width="120" height="120" viewBox="0 0 120 120"><path d="M60 6 A54 54 0 1 0 112 46" fill="none" stroke="#1aa7a0" stroke-width="8" stroke-linecap="round"/><circle cx="60" cy="60" r="38" fill="#d9f1ef" role="img" aria-label="Team meeting icon"/></svg>
    <h3>Quis autem vel eum</h3>
    <p>Sed ut perspiciatis unde omnis iste natus error sit voluptatem accusantium doloremque laudantium, totam rem aperiam, eaque ipsa quae ab illo</p>
  </div>
  <div class="step-card" style="left:614px;top:1460px">
    <svg class="step-icon" width="120" height="120" viewBox="0 0 120 120"><path d="M60 6 A54 54 0 1 0 112 46" fill="none" stroke="#1aa7a0" stroke-width="8" stroke-linecap="round"/><circle cx="60" cy="60" r="38" fill="#d9f1ef" role="img" aria-label="Presenter at a board icon"/></svg>
    <h3>Quis autem vel eum</h3>
    <p>Sed ut perspiciatis unde omnis iste natus error sit voluptatem accusantium doloremque laudantium, totam rem aperiam, eaque ipsa quae ab illo</p>
  </div>
  <div class="step-card" style="left:143px;top:1665px">
    <svg class="step-icon" width="120" height="120" viewBox="0 0 120 120"><path d="M60 6 A54 54 0 1 0 112 46" fill="none" stroke="#1aa7a0" stroke-width="8" stroke-linecap="round"/><circle cx="60" cy="60" r="38" fill="#d9f1ef" role="img" aria-label="Planning chart icon"/></svg>
    <h3>Quis autem vel eum</h3>
    <p>Sed ut perspiciatis unde omnis iste natus error sit voluptatem accusantium doloremque laudantium, totam rem aperiam, eaque ipsa quae ab illo</p>
  </div>
  <div class="step-card" style="left:614px;top:1665px">
    <svg class="step-icon" width="120" height="120" viewBox="0 0 120 120"><path d="M60 6 A54 54 0 1 0 112 46" fill="none" stroke="#1aa7a0" stroke-width="8" stroke-linecap="round"/><circle cx="60" cy="60" r="38" fill="#d9f1ef" role="img" aria-label="Strategy board icon"/></svg>
    <h3>Quis autem vel eum</h3>
    <p>Sed ut perspiciatis unde omnis iste natus error sit voluptatem accusantium doloremque laudantium, totam rem aperiam, eaque ipsa quae ab illo</p>
  </div>
  <svg class="step-hub" width="66" height="66" viewBox="0 0 66 66"><path d="M33 3 L45 15 L38 15 L38 28 L51 28 L51 21 L63 33 L51 45 L51 38 L38 38 L38 51 L45 51 L33 63 L21 51 L28 51 L28 38 L15 38 L15 45 L3 33 L15 21 L15 28 L28 28 L28 15 L21 15 Z" fill="rgba(255,255,255,.15)" stroke="#fff" stroke-width="2"/></svg>

  <!-- testimonials -->
  <div class="section-title" style="left:463px;top:2065px;width:272px">TESTIMONIALS</div>

  <div class="quote" style="left:143px">
    <div class="avatar" role="img" aria-label="Client photo"></div>
    <p class="quote-text"><b>“</b>At vero eos et accusamus et iustodio dignissimos ducimus qui blanditiispraesent ium volutum deleniti atque cruquqcs</p>
    <div class="quote-name">Marcus Hale</div>
    <div class="stars"><svg width="100" height="16" viewBox="0 0 100 16"><g fill="#fff"><path id="s" d="M8 1 L10 6 L15 6 L11 9.5 L12.5 15 L8 11.5 L3.5 15 L5 9.5 L1 6 L6 6 Z"/><use href="#s" x="20"/><use href="#s" x="40"/><use href="#s" x="60"/></g><use href="#s" x="80" fill="none" stroke="#fff" stroke-width="1.2"/></svg></div>
  </div>
  <div class="quote" style="left:452px">
    <div class="avatar" role="img" aria-label="Client photo"></div>
    <p class="quote-text"><b>“</b>At vero eos et accusamus et iustodio dignissimos ducimus qui blanditiispraesent ium volutum deleniti atque cruquqcs</p>
    <div class="quote-name">Marcus Hale</div>
    <div class="stars"><svg width="100" height="16" viewBox="0 0 100 16"><g fill="#fff"><use href="#s"/><use href="#s" x="20"/><use href="#s" x="40"/><use href="#s" x="60"/></g><use href="#s" x="80" fill="none" stroke="#fff" stroke-width="1.2"/></svg></div>
  </div>
  <div class="quote" style="left:767px">
    <div class="avatar" role="img" aria-label="Client photo"></div>
    <p class="quote-text"><b>“</b>At vero eos et accusamus et iustodio dignissimos ducimus qui blanditiispraesent ium volutum deleniti atque cruquqcs</p>
    <div class="quote-name">Marcus Hale</div>
    <div class="stars"><svg width="100" height="16" viewBox="0 0 100 16"><g fill="#fff"><use href="#s"/><use href="#s" x="20"/><use href="#s" x="40"/><use href="#s" x="60"/></g><use href="#s" x="80" fill="none" stroke="#fff" stroke-width="1.2"/></svg></div>
  </div>
  <div class="carousel-arrows">
    <svg width="26" height="26" viewBox="0 0 26 26"><circle cx="13" cy="13" r="11.5" fill="none" stroke="#fff" stroke-width="1.5"/><path d="M15 8 L10 13 L15 18" fill="none" stroke="#fff" stroke-width="1.8"/></svg>
    <svg width="26" height="26" viewBox="0 0 26 26"><circle cx="13" cy="13" r="11.5" fill="none" stroke="#fff" stroke-width="1.5"/><path d="M11 8 L16 13 L11 18" fill="none" stroke="#fff" stroke-width="1.8"/></svg>
  </div>

  <!-- blog -->
  <div class="section-title blue" style="left:472px;top:2612px;width:256px">LATEST BLOG</div>

  <article class="post" style="left:148px">
    <div class="post-image" role="img" aria-label="Business team reviewing charts at a desk" style="background:linear-gradient(135deg,#6f5a4a,#c9b8a4 55%,#3a4650)"></div>
  </article>
  <article class="post" style="left:623px">
    <div class="post-image" role="img" aria-label="Colleagues working on a laptop" style="background:linear-gradient(135deg,#2f5876,#9fb8c8 55%,#d7c6b2)"></div>
  </article>
  <div class="post-caption" style="left:193px;top:2932px">
    <h4>Sed ut perspiciatis unde omnis sit<br>voluptatem accusantium</h4>
    <div class="post-meta"><span>▦ Jan 25, 2019</span><span style="color:#ccc">|</span><span>◯ 2 comments</span></div>
  </div>
  <div class="post-caption" style="left:668px;top:2932px">
    <h4>Sed ut perspiciatis unde omnis sit<br>voluptatem accusantium</h4>
    <div class="post-meta"><span>▦ Jan 25, 2019</span><span style="color:#ccc">|</span><span>◯ 2 comments</span></div>
  </div>

  <!-- footer -->
  <h5 class="foot-title" style="left:143px">SIGN UP TO RECEIVE EMAIL</h5>
  <p class="foot-text">Excepteur sint occaecat cupidatat non proident, sunt in culpa qui Nemo enim ipsam voluptatem</p>
  <div class="signup"><span>Enter Email</span><b>SUBSCRIBE</b></div>

  <h5 class="foot-title" style="left:584px">CONTACT US</h5>
  <div class="contact-row" style="top:3348px">
    <svg width="16" height="20" viewBox="0 0 16 20"><path d="M8 19 C3 12 1.5 9.5 1.5 7 A6.5 6.5 0 0 1 14.5 7 C14.5 9.5 13 12 8 19Z" fill="none" stroke="#fff" stroke-width="1.6"/><circle cx="8" cy="7" r="2.3" fill="none" stroke="#fff" stroke-width="1.5"/></svg>
    <span>Glen Whitmore<br>42 Ridgeline Ave. Boulder<br>CO 80302</span>
  </div>
  <div class="contact-row" style="top:3427px">
    <svg width="16" height="16" viewBox="0 0 16 16"><path d="M3 1 L6 1 L7 5 L5 6.5 C6 9 7 10 9.5 11 L11 9 L15 10 L15 13 C15 14 14 15 13 15 C7 15 1 9 1 3 C1 2 2 1 3 1Z" fill="none" stroke="#fff" stroke-width="1.4"/></svg>
    <span>Phone : 555-014-2290</span>
  </div>
  <div class="contact-row" style="top:3465px">
    <svg width="18" height="14" viewBox="0 0 18 14"><rect x="1" y="1" width="16" height="12" fill="none" stroke="#fff" stroke-width="1.4"/><path d="M1 1 L9 8 L17 1" fill="none" stroke="#fff" stroke-width="1.4"/></svg>
    <span>Email : info@glenwhitmore.com</span>
  </div>

  <h5 class="foot-title" style="left:905px;top:3282px">FOLLOW US</h5>
  <div class="social" aria-label="Social media links"><span></span><span></span><span></span><span></span></div>

  <p class="copyright">Copyright © Glen Whitmore 2019. All rights reserved. | Privacy Policy</p>
</div>
</body>
</html>
```